Redesign of Form/Document Navigation Page

I need a redesign of our document and navigation bar on the left. We want the same navigation bar layout/setup but want the buttons and typography to be simple and matching all over. The form needs to be aesthetically pleasing and fit within the page.

1st attachment is our Direct Deposit and the second is the form continued.

```html
<!DOCTYPE html>
<html lang="en">
<head>
<meta charset="utf-8">
<title>Employee Direct Deposit Enrollment Form</title>
<link rel="stylesheet" href="https://fonts.googleapis.com/css2?family=Roboto:wght@300;400;500;700&family=Noto+Serif:ital@1&display=swap">
<style>
:root{
  --blue:#11528f;
  --blue-dark:#0b3f72;
  --gold:#f0b41c;
  --gold-text:#e8a91a;
  --ink:#1d1d1d;
  --muted:#555;
  --line:#c9c9c9;
  --link:#5b2ea6;
  --scroll:#e6e6e6;
  --thumb:#bdbdbd;
  --bg:#ffffff;
}
*{box-sizing:border-box;margin:0;padding:0}
html,body{width:1200px;height:849px;overflow:hidden;background:var(--bg);font-family:"Roboto",sans-serif;color:var(--ink)}
.page{position:relative;width:1200px;height:849px}
.brand{position:absolute;left:99px;top:21px;display:flex;align-items:center;gap:8px}
.brand-mark{width:40px;height:40px;border-radius:50%;background:var(--blue)}
.brand-name{font-weight:700;font-size:20px;line-height:19px;color:var(--gold-text);text-transform:uppercase;letter-spacing:-.2px}
.topnav{position:absolute;top:32px;left:624px;display:flex;align-items:center;font-weight:500;font-size:14px}
.topnav a{color:var(--ink);text-decoration:none;display:flex;align-items:center;gap:6px}
.topnav .home{width:106px}.topnav .help{width:97px}
.topnav .user{color:var(--blue)}
.btn{background:var(--gold);color:#fff;border:0;font-family:inherit;font-size:13px;font-weight:500;text-transform:uppercase}
.back{position:absolute;left:966px;top:23px;width:134px;height:37px;border-radius:2px}
.sidebar{position:absolute;left:99px;top:93px;width:276px;height:679px;background:var(--blue);border:2px solid var(--blue-dark)}
.sidebar a{display:flex;align-items:center;height:96.7px;padding-left:18px;gap:18px;color:#fff;text-decoration:none;font-weight:500;font-size:15.5px;border-bottom:2px solid var(--blue-dark)}
.sidebar a:last-child{border-bottom:0}
.sidebar svg{width:40px;height:40px;flex:none}
.panel{position:absolute;left:405px;top:93px;width:696px;height:683px;border:1px solid var(--line);overflow:hidden}
.scrollbar{position:absolute;right:0;top:0;width:15px;height:100%;background:var(--scroll)}
.scrollbar span{display:block;height:100px;background:var(--thumb)}
.form{padding:20px 36px 0 22px}
h1{font-size:19.5px;font-weight:500;letter-spacing:.2px;margin-bottom:8px}
.small{font-size:10.8px;line-height:20.5px;color:var(--muted);padding-left:2px}
.lead{font-size:14px;line-height:24px;margin-top:4px}
.attach{margin:14px 0 0 1px;height:99px;border:1px solid var(--line);text-align:center;padding-top:17px}
.attach a{font-size:12px;color:var(--link)}
.refresh{display:block;margin:9px auto 0;width:84px;height:30px;border-radius:2px;font-size:11.5px}
h2{font-size:14px;font-weight:500;margin:22px 0 6px}
.notice{font-size:14px;font-weight:500;margin-top:6px}
.radios{display:flex;gap:22px;margin-top:11px;font-family:"Noto Serif",serif;font-style:italic;font-size:13px;color:#333}
.radios.account-type{margin-top:18px}
.radios label{display:flex;align-items:center;gap:11px}
.radios i{width:13px;height:13px;border:1px solid #aaa;border-radius:50%;background:#f5f5f5}
.grid{display:grid;grid-template-columns:repeat(3,203px);gap:12px 14px;margin:18px 0 0 1px}
.field{height:32px;border:1px solid var(--line);display:flex;align-items:center;justify-content:space-between;padding:0 11px;font-size:11px;font-style:italic;font-weight:300;color:#777}
.field b{font-size:8px;color:#888;font-style:normal}
.important{font-size:14px;margin-top:20px}
.important strong{font-size:16.5px;font-weight:700}
.consent{margin-top:8px}
.footer-line{position:absolute;left:99px;top:804px;width:1002px;border-top:1px solid var(--line)}
.footer{position:absolute;top:819px;left:0;width:1200px;text-align:center;font-size:11px;color:#444}
</style>
</head>
<body>
<div class="page">
  <div class="brand"><span class="brand-mark"></span><span class="brand-name">Sentinel Shield<br>Services</span></div>
  <nav class="topnav">
    <a class="home" href="#">HOME
      <svg width="12" height="11" viewBox="0 0 12 11"><path d="M6 0 0 5.5h1.6V11h3V7.5h2.8V11h3V5.5H12z" fill="#1d1d1d"/></svg></a>
    <a class="help" href="#">HELP <span>?</span></a>
    <a class="user" href="#">DANA REYES
      <svg width="13" height="13" viewBox="0 0 13 13"><path d="M6.5 1v5M3.4 3a4.6 4.6 0 1 0 6.2 0" stroke="#11528f" stroke-width="1.8" fill="none" stroke-linecap="round"/></svg></a>
  </nav>
  <button class="btn back">Back to Profile</button>

  <aside class="sidebar">
    <a href="#"><svg viewBox="0 0 40 40"><circle cx="22" cy="22" r="15" fill="#fff"/><text x="22" y="29" text-anchor="middle" font-size="20" font-weight="700" fill="#11528f" font-family="Roboto,sans-serif">$</text><path d="M6 4v9M2 9l4 5 4-5" stroke="#fff" stroke-width="2.5" fill="none"/></svg>DIRECT DEPOSIT</a>
    <a href="#"><svg viewBox="0 0 40 40"><rect x="2" y="4" width="36" height="26" fill="none" stroke="#fff" stroke-width="2.5"/><path d="M9 12h22M12 17h16" stroke="#fff" stroke-width="2"/><circle cx="24" cy="29" r="6" fill="#fff"/><path d="M21 34v5l3-2 3 2v-5" fill="#fff"/></svg>CHANGE W-4</a>
    <a href="#"><svg viewBox="0 0 40 40"><path d="M6 36 26 14M12 6l10 10M8 10l8-6 6 4-8 6z M34 36 18 20M28 4a6 6 0 0 0 6 8" stroke="#fff" stroke-width="3.5" fill="none" stroke-linecap="round"/></svg>LABOUR CODE</a>
    <a href="#"><svg viewBox="0 0 40 40"><circle cx="20" cy="20" r="17" fill="none" stroke="#fff" stroke-width="2.5"/><circle cx="21" cy="11" r="2.3" fill="#fff"/><path d="M18 16h4l-3 13h3" stroke="#fff" stroke-width="2.6" fill="none"/></svg>PERSONAL INFORMATION</a>
    <a href="#"><svg viewBox="0 0 40 40"><rect x="2" y="18" width="7" height="18" fill="#fff"/><path d="M12 18 20 4c3 0 4 2 3 6l-2 6h11c3 0 4 3 3 5l-3 13c-1 2-2 2-4 2H12z" fill="#fff"/></svg>APPRAISAL &amp; REVIEW</a>
    <a href="#"><svg viewBox="0 0 40 40"><rect x="8" y="4" width="24" height="32" fill="none" stroke="#fff" stroke-width="2.5"/><path d="M13 12h14M13 18h14M13 24h14M13 30h10" stroke="#fff" stroke-width="2.2"/></svg>WRITE-UP SLIP</a>
    <a href="#"><svg viewBox="0 0 40 40"><path d="M4 36h4v-6H4zM10 36h4v-9h-4zM16 36h4V24h-4zM22 36h4V20h-4zM30 36h4V14h-4z" fill="#fff"/><path d="M4 26 28 8" stroke="#fff" stroke-width="2.5"/><path d="M24 5h9v9z" fill="#fff"/></svg>EMPLOYEE PERFORMANCE</a>
  </aside>

  <main class="panel">
    <div class="scrollbar"><span></span></div>
    <div class="form">
      <h1>EMPLOYEE DIRECT DEPOSIT ENROLLMENT FORM</h1>
      <p class="small">To enroll in Direct Deposit, simply fill out this form. Attach a voided check for each checking account - not a deposit slip. If depositing to a savings account, ask your bank to give you the Routing/Transit Number for your account. It isn't always the same as the number on a savings deposit slip. This will help ensure that you are paid correctly.</p>
      <p class="lead">Employees must attach a voided check for each of their accounts to help verify their account numbers and bank routing numbers.</p>
      <div class="attach">
        <a href="#">Attach A Voided Check or Bank Deposit Form For The Account</a>
        <button class="btn refresh">REFRESH</button>
      </div>
      <h2>ACCOUNT INFORMATION</h2>
      <p class="small">The last item must be for the remaining amount owed to you. To distribute to more accounts, please complete another form.</p>
      <p class="lead">Make sure to indicate what kind of account, along with enrolling or declining.</p>
      <p class="notice">*** NOTIFY PAYROLL IMMEDIATELY IF YOU CLOSE OR CHANGE BANK ACCOUNT</p>
      <div class="radios">
        <label><i></i>New Enrollment</label>
        <label><i></i>Change Enrollment</label>
        <label><i></i>Cancel Enrollment</label>
      </div>
      <div class="grid">
        <div class="field">Bank Name</div>
        <div class="field">City <b>▼</b></div>
        <div class="field">State <b>▼</b></div>
        <div class="field">Routing Transit #</div>
        <div class="field">Account number</div>
        <div class="field">Amount <b>%</b></div>
      </div>
      <div class="radios account-type">
        <label><i></i>Checking</label>
        <label><i></i>Saving</label>
      </div>
      <p class="important"><strong>IMPORTANT!</strong> PLEASE READ AND SIGN BEFORE COMPLETING AND SUBMITTING</p>
      <p class="small consent">I hereby authorize SENTINEL SHIELD SERVICES to deposit any amounts owed me, as instructed by my employer, by initiating credit entries to my account at the financial institution (hereinafter Bank) indicated on this form. Further, I authorize Bank to accept and to credit any credit entries indicated by SENTINEL SHIELD SERVICES to my account.</p>
    </div>
  </main>

  <div class="footer-line"></div>
  <p class="footer">© 2016 Company name, Inc. All rights reserved.</p>
</div>
</body>
</html>
```